Powerpoint and Word template required

We need PowerPoint and Word templates for all of our company branded materials and stationary. We have recently rebranded our website and would like something that is reflective of our new corporate branding. A sample of some of the documents we have created recently are attached and our website is below

http://lorwynmedical.com.au/

The word template will be used for all letters we send to clients and customers and we think we want the logo and ISO 9001 cert to only appear on the first page.

The powerpoint template has to be flexible as we use this for both marketing and training purposes. I have attached a couple of samples of the types of documents we create and note that these are very basic / crude and we would be looking for something that is a significant improvement on these

In the powerpoint template it would be good to have lots of standard layouts within the template, e.g. different 'standard layouts for multiple elements on a page including pictures and text etc.
Updates

Project Deadline Extended
Reason: Still looking for a professional yet modern template and important to us that we can see more tan just a title slide and the layout of the other slide master slides is very important to us. Many thanks, Dale

Industry/Entity Type

Healthcare

Font styles to use
Sans Serif

Colors
33a6d7

Requirements
Must have
• Templates must be versatile for use; powerpoint template must be able to be used for training materials and weel as marketing / pitch books.
• Word template must be able to be used as a basis for our corporate letter head through to RFP response type documents as well as Reference / Operating manual type of documents
• In terms of the design it must be consistent with our new corporate image which is best represented by our new website design; www.lorwynmedical.com

```html
<!DOCTYPE html>
<html lang="en">
<head>
<meta charset="UTF-8">
<title>Lorwyn Healthcare – Section Divider</title>
<link rel="stylesheet" href="https://fonts.googleapis.com/css2?family=Roboto+Condensed:wght@400;700&display=swap">
<style>
  :root {
    --brand-blue: #2581c5;
    --brand-blue-soft: #2f8acb;
    --band-light: #eef3fa;
    --logo-blue: #2a7fc3;
    --text-grey: #4a4f55;
    --white: #ffffff;
    --ink: #232323;
  }
  * { margin: 0; padding: 0; box-sizing: border-box; }
  html, body {
    width: 1200px;
    height: 900px;
    overflow: hidden;
    background: var(--band-light);
    font-family: "Roboto Condensed", "Arial Narrow", sans-serif;
  }
  .slide {
    position: relative;
    width: 1200px;
    height: 900px;
    background: var(--band-light);
    overflow: hidden;
  }
  .header {
    position: absolute;
    top: 0; left: 0;
    width: 100%;
    height: 96px;
    background: linear-gradient(180deg, #f3f7fc 0%, var(--band-light) 100%);
  }
  .brand {
    position: absolute;
    top: 30px;
    right: 28px;
    display: flex;
    align-items: center;
    gap: 10px;
  }
  .brand-mark {
    width: 50px;
    height: 50px;
    background: var(--logo-blue);
    border-radius: 5px;
  }
  .brand-name {
    font-size: 52px;
    font-weight: 700;
    color: var(--logo-blue);
    line-height: 1;
  }
  .section-band {
    position: absolute;
    top: 96px; left: 0;
    width: 100%;
    height: 696px;
    background: var(--brand-blue);
    display: flex;
    align-items: center;
    justify-content: center;
  }
  .band-accent {
    position: absolute;
    left: 0;
    top: 196px;
    width: 405px;
    height: 500px;
    background: var(--brand-blue-soft);
  }
  .section-title {
    position: relative;
    font-size: 78px;
    font-weight: 700;
    letter-spacing: 2px;
    color: var(--white);
    text-transform: uppercase;
    margin-top: 2px;
  }
  .footer {
    position: absolute;
    bottom: 0; left: 0;
    width: 100%;
    height: 108px;
    background: linear-gradient(180deg, var(--band-light) 0%, #f4f7fb 100%);
  }
  .copyright {
    position: absolute;
    left: 0;
    top: 46px;
    width: 198px;
    height: 47px;
    background: var(--brand-blue);
    color: var(--white);
    font-size: 20px;
    display: flex;
    align-items: center;
    justify-content: center;
  }
  .web-address {
    position: absolute;
    left: 0; right: 0;
    top: 56px;
    text-align: center;
    font-size: 20px;
    color: var(--text-grey);
    word-spacing: 4px;
  }
  .page-number {
    position: absolute;
    right: 12px;
    top: 57px;
    width: 42px;
    height: 42px;
    background: var(--ink);
    border-radius: 5px;
    color: var(--white);
    font-size: 20px;
    font-weight: 700;
    display: flex;
    align-items: center;
    justify-content: center;
  }
</style>
</head>
<body>
  <main class="slide">
    <header class="header">
      <div class="brand">
        <span class="brand-mark" aria-hidden="true"></span>
        <span class="brand-name">Lorwyn</span>
      </div>
    </header>

    <section class="section-band">
      <div class="band-accent" aria-hidden="true"></div>
      <h1 class="section-title">Section Divider Here</h1>
    </section>

    <footer class="footer">
      <div class="copyright">Copyright text here</div>
      <div class="web-address">||&nbsp; www.lorwynmedical.com.au &nbsp;||</div>
      <div class="page-number">01</div>
    </footer>
  </main>
</body>
</html>
```